Business Card Design

Business Card for professional consulting firm working with large financial institutions.

Target Market(s)

Executive buyers

Industry/Entity Type

Banking

Contact Information for Business Card

Mild creativity wanted. Not boring, but do elaborate artwork.

Font styles to use
Serif
Sans Serif

Colors

Designer to choose colors to be used in the design.

Requirements
Must have
• Standard business card features - company name, individual name, telephone, website, email, locations.
Nice to have
• Two colors
Should not have
• too many colors, fancy printing, cartoons.

```html
<!DOCTYPE html>
<html lang="en">
<head>
<meta charset="utf-8">
<title>k7advisory Business Card</title>
<link href="https://fonts.googleapis.com/css2?family=Merriweather:wght@400&family=Roboto:wght@400;500&display=swap" rel="stylesheet">
<style>
  :root {
    --backdrop: #b4b4b4;
    --ink: #000000;
    --paper: #f4f4f4;
    --swoosh: #bdbdbd;
    --text-dark: #3a3a3a;
    --text-light: #ffffff;
  }
  * { margin: 0; padding: 0; box-sizing: border-box; }
  html, body {
    width: 1200px; height: 960px; overflow: hidden;
    background: var(--backdrop);
  }
  .canvas { position: relative; width: 1200px; height: 960px; }
  .card {
    position: absolute; width: 600px; height: 342px; overflow: hidden;
  }
  .card-front { left: 322px; top: 108px; background: var(--paper); }
  .card-back { left: 320px; top: 493px; background: var(--ink); }
  .front-shapes { position: absolute; inset: 0; }
  .person {
    position: absolute; right: 30px; top: 14px; text-align: right;
    font-family: "Roboto", sans-serif; color: var(--text-light);
  }
  .person-name { font-size: 19px; font-weight: 500; line-height: 24px; }
  .person-role { font-size: 14px; line-height: 18px; }
  .brand-name {
    position: absolute; left: 48px; top: 152px;
    font-family: "Merriweather", serif; font-size: 27px; color: var(--ink);
  }
  .contact-list {
    position: absolute; left: 32px; top: 261px; list-style: none;
    font-family: "Roboto", sans-serif; font-size: 14px; color: var(--text-dark);
  }
  .contact-list li { display: flex; align-items: center; height: 19px; }
  .contact-list svg { width: 13px; height: 13px; margin-right: 7px; fill: var(--ink); }
  .address {
    position: absolute; right: 30px; top: 263px; text-align: right;
    font-family: "Roboto", sans-serif; font-size: 14px; line-height: 18.5px;
    color: var(--text-dark);
  }
  .back-brand {
    position: absolute; left: 0; right: 0; top: 134px; text-align: center;
    font-family: "Merriweather", serif; font-size: 50px; color: var(--text-light);
  }
</style>
</head>
<body>
<main class="canvas">
  <section class="card card-front">
    <svg class="front-shapes" viewBox="0 0 600 342" width="600" height="342">
      <rect width="600" height="342" fill="var(--ink)"/>
      <path d="M0,106 C160,60 430,50 600,72 L600,342 L0,342 Z" fill="var(--paper)"/>
      <path d="M0,106 C180,56 470,48 560,80 C600,96 602,140 560,200 C588,150 584,110 548,94 C450,64 200,70 0,112 Z" fill="var(--swoosh)"/>
    </svg>
    <div class="person">
      <div class="person-name">DANIEL REYES</div>
      <div class="person-role">CEO/Founder</div>
    </div>
    <div class="brand-name">k7advisory</div>
    <ul class="contact-list">
      <li><svg viewBox="0 0 24 24"><path d="M6.6 10.8a15 15 0 006.6 6.6l2.2-2.2c.3-.3.7-.4 1-.2 1.1.4 2.3.6 3.6.6.6 0 1 .4 1 1V20c0 .6-.4 1-1 1A17 17 0 013 4c0-.6.4-1 1-1h3.5c.6 0 1 .4 1 1 0 1.3.2 2.5.6 3.6.1.3 0 .7-.2 1z"/></svg>555 014 2290</li>
      <li><svg viewBox="0 0 24 24"><path d="M2 5h20v14H2z M4 7v.5l8 5 8-5V7l-8 5z" fill-rule="evenodd"/></svg>info@k7advisory.com</li>
      <li><svg viewBox="0 0 24 24"><circle cx="12" cy="12" r="10"/></svg>www.k7advisory.com</li>
    </ul>
    <div class="address">
      <div>k7advisory</div>
      <div>2146 Willow Creek Lane</div>
      <div>Fairview, Alaska 99502</div>
    </div>
  </section>
  <section class="card card-back">
    <div class="back-brand">k7advisory</div>
  </section>
</main>
</body>
</html>
```